Operator Qualification Testing Flyer

I have a 8x10 basic flyer that I created usin InDesign for one of our services our company provides. I would like to see more options for the layout and general design of the flyer. This flyer will be used as a template for the other services we provide. I will include the InDesign Folder with all the logos and images. Please feel free to use any logo design within the folder and you can change the font and/or colors as needed. I would like the final output in a Indesign package folder to be used in InDesign 2021

Target Market(s)

Business to Business marketing in the Oil and Gas industry

Font styles to use
Sans Serif

Colors
85cae6
85acd3
3377b5
0355a3
0792cd
ffffff
cedeed

Requirements
Must have
• I included/attached a couple of brochures styles that I do like.

```html
<!DOCTYPE html>
<html lang="en">
<head>
<meta charset="utf-8">
<title>Pipeline OQ Testing Flyer</title>
<link href="https://fonts.googleapis.com/css2?family=Open+Sans:wght@400;600;700;800&display=swap" rel="stylesheet">
<style>
  :root {
    --steel-blue: #4f7f9f;
    --deep-blue: #3a6d8f;
    --heading-blue: #2f5f80;
    --ring-blue: #5b8db0;
    --pale-gray: #d9dde2;
    --light-gray: #e9ecef;
    --text-dark: #2b3138;
    --white: #ffffff;
    --backdrop: #eef1f4;
    --photo-earth: #8d7d63;
    --photo-earth-dark: #6f6450;
    --sign-yellow: #d8a920;
  }
  * { margin: 0; padding: 0; box-sizing: border-box; }
  html, body { width: 1200px; height: 855px; overflow: hidden; background: var(--backdrop); }
  body { font-family: "Open Sans", Arial, sans-serif; color: var(--text-dark); }
  .flyer {
    position: absolute; left: 280px; top: 27px; width: 640px; height: 800px;
    background: var(--white); overflow: hidden; box-shadow: 0 4px 18px rgba(0,0,0,.12);
  }
  .flyer-shapes { position: absolute; inset: 0; }
  .brand { position: absolute; left: 42px; top: 62px; display: flex; align-items: center; gap: 8px; }
  .brand-mark { width: 22px; height: 22px; border-radius: 50%; background: var(--deep-blue); }
  .brand-name { font-weight: 700; font-size: 13px; color: var(--text-dark); line-height: 1.1; }
  .title {
    position: absolute; left: 52px; top: 196px; color: var(--white);
    font-weight: 800; font-size: 52px; line-height: 1.02; letter-spacing: 1px;
  }
  .section { position: absolute; }
  .section h2 {
    font-size: 16px; font-weight: 700; color: var(--heading-blue); line-height: 1.1;
    display: inline-block; padding-bottom: 4px; border-bottom: 2px solid var(--heading-blue); margin-bottom: 7px;
  }
  .section p { font-size: 10px; line-height: 1.45; color: var(--text-dark); }
  .sec-oq { left: 40px; top: 402px; width: 318px; }
  .sec-tasks { left: 40px; top: 590px; width: 205px; }
  .sec-program { left: 272px; top: 590px; width: 245px; }
  .footer-note {
    position: absolute; left: 30px; top: 750px; width: 580px;
    color: var(--white); font-size: 10px; line-height: 1.45;
  }
</style>
</head>
<body>
  <main class="flyer">
    <svg class="flyer-shapes" width="640" height="800" viewBox="0 0 640 800">
      <defs>
        <clipPath id="hero-clip"><circle cx="585" cy="170" r="260"/></clipPath>
        <clipPath id="detail-clip"><circle cx="480" cy="440" r="100"/></clipPath>
        <linearGradient id="earth" x1="0" y1="0" x2="1" y2="1">
          <stop offset="0" stop-color="var(--photo-earth)"/>
          <stop offset="1" stop-color="var(--photo-earth-dark)"/>
        </linearGradient>
      </defs>
      <polygon class="band-gray" points="0,140 400,112 408,140 0,168" fill="var(--pale-gray)"/>
      <polygon class="band-blue" points="0,168 408,140 425,320 0,372" fill="var(--steel-blue)"/>
      <polygon class="band-light" points="0,372 425,320 432,340 0,394" fill="var(--light-gray)"/>
      <circle cx="585" cy="170" r="290" fill="none" stroke="var(--ring-blue)" stroke-width="1.2"/>
      <circle cx="585" cy="170" r="273" fill="none" stroke="var(--ring-blue)" stroke-width="20"/>
      <g role="img" aria-label="Excavator digging a pipeline trench beside exposed green pipes">
        <rect x="300" y="0" width="340" height="440" fill="url(#earth)" clip-path="url(#hero-clip)"/>
      </g>
      <circle cx="480" cy="440" r="114" fill="none" stroke="var(--ring-blue)" stroke-width="1.2"/>
      <circle cx="480" cy="440" r="106" fill="var(--white)"/>
      <g role="img" aria-label="Aerial view of a side-boom tractor lowering pipe into a trench">
        <rect x="380" y="340" width="200" height="200" fill="url(#earth)" clip-path="url(#detail-clip)"/>
      </g>
      <circle cx="373" cy="400" r="7" fill="var(--deep-blue)"/>
      <circle cx="435" cy="544" r="7" fill="var(--deep-blue)"/>
      <line x1="590" y1="395" x2="640" y2="372" stroke="var(--ring-blue)" stroke-width="1.2"/>
      <g role="img" aria-label="Yellow petroleum pipeline warning marker">
        <circle cx="586" cy="620" r="44" fill="var(--sign-yellow)"/>
      </g>
      <polygon class="band-footer" points="0,738 640,722 640,800 0,800" fill="var(--steel-blue)"/>
      <line x1="0" y1="797" x2="640" y2="785" stroke="var(--pale-gray)" stroke-width="2"/>
    </svg>

    <div class="brand">
      <span class="brand-mark"></span>
      <span class="brand-name">Meridian Field<br>Services Inc.</span>
    </div>

    <h1 class="title">PIPELINE<br>OQ<br>TESTING</h1>

    <section class="section sec-oq">
      <h2>What Is<br>Operator Qualification?</h2>
      <p>Operator Qualifications (OQ) for DOT Oil/Gas Pipelines are requirements set by Department of Transportation (DOT) and Pipeline and Hazardous Materials Safety Administration (PHMSA). To assure safety in the transport of hazardous gases and liquids in the nation's pipelines, pipeline operators who perform covered tasks must be qualified. Qualified means that an individual has been evaluated and can perform assigned covered tasks and recognize and react to abnormal operating conditions.</p>
    </section>

    <section class="section sec-tasks">
      <h2>What Are<br>Covered Tasks?</h2>
      <p>Covered tasks are defined in an operator's written plan which defines specific job functions or activities personnel are qualified to perform on a pipeline facility.</p>
    </section>

    <section class="section sec-program">
      <h2>What Are<br>Covered Tasks?</h2>
      <p>Meridian Field Services Inc. utilizes NCTR pipeline program to administer OQ assessment testing on 127 covered tasks. Upon completion of OQ testing the information is first transferred to NCTR's Registry System and automatically uploaded to VendorLink.</p>
    </section>

    <p class="footer-note">In addition to the benefits provided by VendorLink's database, the NCTR Registry System houses all the completion information allowing candidates to share their training information and employers to verify successful covered task and level completions.</p>
  </main>
</body>
</html>
```